Create a memorable Web Design for real estate branding

we are a Minnepolis brokerage and boutique housing specialist with over 27 years of experience in the Global furnished housing industry, servicing the Greater Los Angeles area. Specializing in “warm environments” we offer a customized approach to satisfying our guests and client’s needs by offering a wide array of options in highly desirable areas. Additionally, Lantern Dwelling Partners offers assistance and expertise to home buyers, sellers and investors.

Industry/Entity Type

Real Estate

Number of Pages Required

1 page

Font styles to use
Serif
Sans Serif
Decorative

```html
<!DOCTYPE html>
<html lang="en">
<head>
<meta charset="utf-8">
<title>Brightmoor Haven Real Estate</title>
<link href="https://fonts.googleapis.com/css2?family=Cinzel:wght@400;700&family=Open+Sans:wght@400;600&display=swap" rel="stylesheet">
<style>
:root{
  --teal:#17a58a;
  --teal-dark:#11876f;
  --lime:#8dc63f;
  --black:#0a0a0a;
  --ink:#222;
  --grey-text:#555;
  --pale:#f1f1f1;
  --line:#d6d6d6;
  --footer:#1f252b;
  --white:#fff;
}
*{box-sizing:border-box;margin:0;padding:0}
html,body{width:1200px;height:2808px;overflow:hidden}
body{font-family:"Open Sans",Arial,sans-serif;color:var(--ink);background:var(--white);position:relative}
.serif{font-family:"Cinzel",Georgia,serif}
a{color:inherit;text-decoration:none}

/* header */
.site-header{position:absolute;top:0;left:0;width:1200px;height:165px;background:var(--black);color:var(--white)}
.topbar{height:34px;border-bottom:2px solid var(--teal);display:flex;align-items:center;justify-content:space-between;padding:0 80px;font-size:13px;color:#ddd}
.topbar .contact{display:flex;gap:26px;align-items:center}
.topbar .contact span{display:flex;gap:8px;align-items:center}
.topbar .social{display:flex;gap:18px}
.topbar .social i{display:block;width:12px;height:12px;border-radius:50%;background:#ccc}
.brand{position:absolute;left:80px;top:62px;font-family:"Cinzel",Georgia,serif;font-weight:700;font-size:30px;line-height:36px;color:var(--teal);display:flex;align-items:center;gap:12px}
.brand .mark{width:22px;height:22px;background:var(--teal)}
.cta{position:absolute;left:844px;top:56px;width:277px;height:47px;background:var(--lime);color:var(--black);font-family:"Cinzel",Georgia,serif;font-weight:700;font-size:16px;display:flex;align-items:center;justify-content:center}
.main-nav{position:absolute;right:79px;top:126px;display:flex;font-size:15px;font-weight:600}
.main-nav a{padding:0 12px;border-left:1px solid #777;line-height:16px}
.main-nav a:first-child{border-left:0;color:var(--lime)}
.main-nav a:last-child{padding-right:0}

/* hero */
.hero{position:absolute;top:165px;left:0;width:1200px;height:511px;background:linear-gradient(180deg,#6b4b2e 0%,#a07a52 40%,#d9cbb6 75%,#c6aa86 100%)}
.hero-caption{position:absolute;left:88px;top:175px;width:1018px;height:106px;background:rgba(0,0,0,.6);color:var(--white);font-family:"Cinzel",Georgia,serif;font-weight:700;font-size:30px;line-height:38px;text-align:center;display:flex;align-items:center;justify-content:center;padding:0 20px}
.hero-arrows{position:absolute;left:567px;top:447px;display:flex;gap:8px}
.hero-arrows span{width:30px;height:30px;border-radius:50%;background:var(--white);display:flex;align-items:center;justify-content:center}
.hero-arrows span.active{background:var(--lime)}

/* welcome */
.welcome{position:absolute;top:676px;left:0;width:1200px;height:664px;background:var(--pale);text-align:center}
.welcome h2{margin-top:42px;font-family:"Cinzel",Georgia,serif;font-size:34px;font-weight:400;color:var(--ink)}
.welcome h2 .accent{color:var(--teal)}
.welcome .intro{width:1040px;margin:32px auto 0;font-size:14.5px;line-height:21px;color:var(--ink)}
.offers{position:absolute;top:221px;left:150px;display:flex;gap:105px}
.offer{width:398px}
.offer .photo{height:264px}
.offer h3{margin-top:16px;font-weight:400;font-size:19px}
.offer p{margin-top:6px;font-size:14.5px;line-height:21px}

/* why choose */
.why{position:absolute;top:1340px;left:0;width:1200px;height:528px;background:var(--white);text-align:center}
.section-title{font-family:"Cinzel",Georgia,serif;font-weight:700;font-size:25px;color:var(--ink)}
.why .section-title{margin-top:54px;display:inline-block;padding-bottom:14px;border-bottom:1px solid var(--line);width:230px}
.features{position:absolute;top:130px;left:88px;width:1024px;display:grid;grid-template-columns:repeat(3,341px);row-gap:48px}
.feature{display:flex;flex-direction:column;align-items:center}
.feature .icon{width:98px;height:98px;border-radius:50%;border:2px solid #222;display:flex;align-items:center;justify-content:center}
.feature .icon.active{background:var(--teal);border-color:var(--teal)}
.feature h4{margin-top:14px;font-weight:400;font-size:19px}

/* three columns */
.panels{position:absolute;top:1868px;left:0;width:1200px;height:532px;background:#f3f3f3}
.panel{position:absolute;top:0}
.panel-head{position:absolute;top:56px;display:flex;justify-content:space-between;align-items:center;font-family:"Cinzel",Georgia,serif;font-size:24px;color:var(--ink)}
.panel-head .nav{font-family:"Open Sans",sans-serif;font-size:20px;color:#777;border-bottom:1px solid #bbb}
.card{position:absolute;top:120px;height:352px;background:var(--white);border:2px solid #cfcfcf;box-shadow:0 2px 6px rgba(0,0,0,.15)}
.listing{left:80px;width:300px}
.listing .photo{margin:10px;height:158px}
.listing h5{margin:10px 12px 0;font-weight:400;font-size:17px}
.listing .sub{margin:2px 12px 0;font-size:13px;color:var(--grey-text);padding-bottom:10px;border-bottom:1px solid #ddd}
.listing .row{display:flex;justify-content:space-between;align-items:center;margin:14px 12px 0}
.tag{background:var(--teal);color:var(--white);font-size:14px;padding:6px 12px}
.price{color:var(--teal);font-weight:600;font-size:23px}
.specs{display:flex;justify-content:space-between;margin:20px 12px 0;padding-top:10px;border-top:1px solid #ddd;font-size:13px;color:var(--grey-text)}
.inquiry{left:438px;width:328px;padding:12px 14px}
.inquiry .field{height:43px;border:1px solid #ccc;margin-bottom:15px;padding:10px 12px;font-size:14px;color:#aaa}
.inquiry .field.tall{height:92px}
.submit{display:inline-block;background:var(--teal);color:var(--white);font-family:"Cinzel",Georgia,serif;font-weight:700;font-size:20px;padding:8px 24px}
.review{left:794px;width:327px;padding:22px 14px}
.review .who{display:flex;align-items:center;gap:10px}
.avatar{width:122px;height:122px;border-radius:50%;border:3px solid #ddd}
.who .name{font-family:"Cinzel",Georgia,serif;font-size:19px;color:var(--teal)}
.who .role{font-family:"Cinzel",Georgia,serif;font-size:19px;color:var(--ink)}
.quote{margin-top:26px;font-size:12.5px;line-height:19px;font-style:italic;color:#333}

/* footer */
.site-footer{position:absolute;top:2400px;left:0;width:1200px;height:363px;background:linear-gradient(180deg,#1a2026,#2b343c);color:var(--white)}
.foot-col{position:absolute;top:60px}
.foot-col h6{font-family:"Cinzel",Georgia,serif;font-weight:400;font-size:21px;margin-bottom:24px}
.foot-col h6 span{color:var(--lime)}
.links li{list-style:none;font-size:13.5px;margin-bottom:24px}
.links li::before{content:"›";margin-right:10px}
.contact-line{display:flex;gap:16px;align-items:flex-start;font-size:14px;line-height:20px;margin-bottom:30px}
.contact-line .sq{width:32px;height:32px;flex:none;background:var(--lime);display:flex;align-items:center;justify-content:center}
.follow li{list-style:none;display:flex;align-items:center;gap:18px;font-size:12px;margin-bottom:15px}
.follow .dot{width:38px;height:38px;border-radius:50%}
.foot-brand{position:absolute;left:842px;top:178px;font-family:"Cinzel",Georgia,serif;font-weight:700;font-size:28px;color:#b9b9b9;display:flex;align-items:center;gap:12px}
.foot-brand .mark{width:20px;height:20px;background:#b9b9b9}
.copyright{position:absolute;top:2763px;left:0;width:1200px;height:45px;background:var(--teal);color:var(--white);font-size:14px;display:flex;align-items:center;justify-content:center}
</style>
</head>
<body>

<header class="site-header">
  <div class="topbar">
    <div class="contact">
      <span>
        <svg width="12" height="12" viewBox="0 0 24 24"><path fill="#ddd" d="M6.6 10.8a15 15 0 0 0 6.6 6.6l2.2-2.2a1 1 0 0 1 1-.25 11.4 11.4 0 0 0 3.6.57 1 1 0 0 1 1 1V20a1 1 0 0 1-1 1A17 17 0 0 1 3 4a1 1 0 0 1 1-1h3.5a1 1 0 0 1 1 1c0 1.25.2 2.45.57 3.57a1 1 0 0 1-.25 1z"/></svg>
        555-014-2290
      </span>
      <span>
        <svg width="13" height="10" viewBox="0 0 26 20"><rect width="26" height="20" fill="#ddd"/><path d="M0 0l13 10L26 0" stroke="#000" stroke-width="2" fill="none"/></svg>
        hello@brightmoorhaven.com
      </span>
    </div>
    <div class="social"><i></i><i></i><i></i><i></i></div>
  </div>
  <div class="brand"><span class="mark"></span>Brightmoor Haven Real Estate</div>
  <a class="cta">Schedule Free Consultation</a>
  <nav class="main-nav">
    <a>FIND A HOME</a><a>SELL YOUR HOME</a><a>HEARTH BLOG</a><a>OUR AGENTS</a><a>CONTACT US</a>
  </nav>
</header>

<section class="hero" role="img" aria-label="Photo of an elegant banquet hall with chandeliers and dressed tables">
  <div class="hero-caption">Lantern Dwelling Partners offers assistance and expertise to home buyers, sellers and investors.</div>
  <div class="hero-arrows">
    <span><svg width="10" height="12" viewBox="0 0 10 12"><path d="M7 1L2 6l5 5" stroke="#222" stroke-width="2" fill="none"/></svg></span>
    <span class="active"><svg width="10" height="12" viewBox="0 0 10 12"><path d="M3 1l5 5-5 5" stroke="#fff" stroke-width="2" fill="none"/></svg></span>
  </div>
</section>

<section class="welcome">
  <h2>WELCOME TO <span class="accent">Brightmoor Haven Real Estate</span></h2>
  <p class="intro">Lorem ipsum dolor sit amet, consectetuer adipiscing elit, sed diam nonummy nibh euismod tincidunt ut laoreet dolore magna aliquam erat volutpat. Ut wisi enim ad minim veniam, quis nostrud exerci tation ullamcorper suscipit lobortis nisl ut aliquip ex ea commodo consequat. Duis autem vel eum iriure dolor in hendrerit in vulputate velit esse molestie consequat, vel illum dolore eu feugiat nulla facilisis at vero</p>
  <div class="offers">
    <div class="offer">
      <div class="photo" role="img" aria-label="Photo of a modern lounge interior with round ceiling panels" style="background:linear-gradient(180deg,#c98a52 0%,#8a7a6c 45%,#5a4a3c 100%)"></div>
      <h3>BUY WITH US</h3>
      <p>Lorem ipsum dolor sit amet, consectetuer adipiscing elit, sed diam nonummy nibh euismod tincidunt ut laoreet dolore magna aliquam erat volutpat. Ut wisi enim ad minim veniam,</p>
    </div>
    <div class="offer">
      <div class="photo" role="img" aria-label="Photo of a couple shaking hands with an agent outside a house" style="background:linear-gradient(180deg,#9fb8d4 0%,#d8d4cc 40%,#6f8f4a 100%)"></div>
      <h3>SELL WITH US</h3>
      <p>Lorem ipsum dolor sit amet, consectetuer adipiscing elit, sed diam nonummy nibh euismod tincidunt ut laoreet dolore magna aliquam erat volutpat. Ut wisi enim ad minim veniam,</p>
    </div>
  </div>
</section>

<section class="why">
  <h2 class="section-title">WHY CHOOSE US</h2>
  <div class="features">
    <div class="feature">
      <div class="icon active"><svg width="48" height="48" viewBox="0 0 48 48"><circle cx="14" cy="10" r="5" fill="#fff"/><rect x="9" y="17" width="10" height="20" rx="3" fill="#fff"/><circle cx="32" cy="24" r="10" fill="none" stroke="#fff" stroke-width="3"/><text x="32" y="30" font-size="15" text-anchor="middle" fill="#fff" font-family="Arial">$</text></svg></div>
      <h4>A PROVEN BROKERAGE</h4>
    </div>
    <div class="feature">
      <div class="icon"><svg width="50" height="40" viewBox="0 0 50 40"><rect x="4" y="14" width="42" height="20" fill="#222"/><circle cx="25" cy="24" r="6" fill="#fff"/><path d="M10 12l26-8 3 8" stroke="#222" stroke-width="3" fill="none"/></svg></div>
      <h4>NO JUNK FEES</h4>
    </div>
    <div class="feature">
      <div class="icon"><svg width="50" height="44" viewBox="0 0 50 44"><rect x="4" y="4" width="42" height="28" fill="none" stroke="#222" stroke-width="3"/><rect x="21" y="32" width="8" height="6" fill="#222"/><rect x="14" y="38" width="22" height="3" fill="#222"/><path d="M16 12h18l-4 12h-10z" fill="#222"/></svg></div>
      <h4>PROFESSIONAL MARKETING</h4>
    </div>
    <div class="feature">
      <div class="icon"><svg width="44" height="48" viewBox="0 0 44 48"><rect x="6" y="4" width="26" height="38" fill="none" stroke="#222" stroke-width="3"/><path d="M12 14h14M12 21h14M12 28h8" stroke="#222" stroke-width="2"/><path d="M24 38l14-16 4 4-14 16h-4z" fill="#222"/></svg></div>
      <h4>ELECTRONIC SIGNATURES</h4>
    </div>
    <div class="feature">
      <div class="icon"><svg width="40" height="50" viewBox="0 0 40 50"><rect x="8" y="4" width="22" height="40" rx="3" fill="none" stroke="#222" stroke-width="3"/><path d="M14 28l6-6 6 6" stroke="#222" stroke-width="3" fill="none"/><circle cx="19" cy="39" r="2" fill="#222"/></svg></div>
      <h4>DIGITAL MARKETING EXPERTS</h4>
    </div>
    <div class="feature">
      <div class="icon"><svg width="50" height="50" viewBox="0 0 50 50"><circle cx="25" cy="20" r="6" fill="#222"/><path d="M15 38a10 10 0 0 1 20 0z" fill="#222"/><g fill="#222"><circle cx="10" cy="12" r="3"/><circle cx="40" cy="12" r="3"/><circle cx="8" cy="30" r="3"/><circle cx="42" cy="30" r="3"/><circle cx="25" cy="5" r="3"/></g><path d="M10 12l10 6M40 12l-10 6M8 30l10-4M42 30l-10-4M25 5v9" stroke="#222" stroke-width="1.5"/></svg></div>
      <h4>OUR VENDOR NETWORK</h4>
    </div>
  </div>
</section>

<section class="panels">
  <div class="panel-head" style="left:80px;width:319px">FEATURED LISTINGS <span class="nav">‹ ›</span></div>
  <div class="panel-head" style="left:438px;width:328px">QUICK INQUIRY</div>
  <div class="panel-head" style="left:794px;width:327px">CUSTOMER REVIEWS <span class="nav">‹ ›</span></div>

  <div class="card listing">
    <div class="photo" role="img" aria-label="Photo of a large stone family house under blue sky" style="background:linear-gradient(180deg,#3a6fc1 0%,#a9b7c8 50%,#5d7a3e 100%)"></div>
    <h5>123 Dollar Smit Amet</h5>
    <p class="sub">Duis autem vel eum iriure</p>
    <div class="row"><span class="tag">For Rent</span><span class="price">$ 123, 000</span></div>
    <div class="specs"><span>1200 sq ft</span><span>2 Beds</span><span>2 Baths</span></div>
  </div>

  <div class="card inquiry">
    <div class="field">Your name</div>
    <div class="field">Your email</div>
    <div class="field">Your phone number</div>
    <div class="field tall">Your message</div>
    <span class="submit">SUBMIT</span>
  </div>

  <div class="card review">
    <div class="who">
      <div class="avatar" role="img" aria-label="Portrait photo of the reviewer" style="background:linear-gradient(180deg,#7a4a32,#d8a98a)"></div>
      <div><div class="name">Maren Holt</div><div class="role">Designation</div></div>
    </div>
    <p class="quote">“ Lorem ipsum dolor sit amet, consece dipiscing elit, sed dianonummy nibh euismod tincid ut laoreet dolore magna aliquam erat dipiscing elit, anonummy erat dipiscing elit, sed dianonummy nibh euismod nibh euismod tincidunt ut laoreet dolore magna aliquam erat dipiscing elit, sed dianonummy nibh euismod volutpat. Utwisi enim ad minim. ”</p>
  </div>
</section>

<footer class="site-footer" role="img" aria-label="Dimmed city skyline at dusk behind the footer">
  <div class="foot-col" style="left:80px">
    <h6>QUICK <span>LINKS</span></h6>
    <ul class="links"><li>Find A Home</li><li>Sell Your Home</li><li>Hearth Blog</li><li>Our Agents</li><li>Contact Us</li></ul>
  </div>
  <div class="foot-col" style="left:300px">
    <h6>CONTACT <span>DETAILS</span></h6>
    <div class="contact-line"><span class="sq"><svg width="14" height="18" viewBox="0 0 14 18"><path d="M7 0a7 7 0 0 0-7 7c0 5 7 11 7 11s7-6 7-11a7 7 0 0 0-7-7z" fill="#fff"/><circle cx="7" cy="7" r="2.5" fill="#8dc63f"/></svg></span><div><b>Office:</b><br>123, Lorem ipsum dolor<br>sit amet, consecte 32145</div></div>
    <div class="contact-line" style="margin-top:34px"><span class="sq"><svg width="16" height="16" viewBox="0 0 24 24"><path fill="#fff" d="M6.6 10.8a15 15 0 0 0 6.6 6.6l2.2-2.2a1 1 0 0 1 1-.25 11.4 11.4 0 0 0 3.6.57 1 1 0 0 1 1 1V20a1 1 0 0 1-1 1A17 17 0 0 1 3 4a1 1 0 0 1 1-1h3.5a1 1 0 0 1 1 1c0 1.25.2 2.45.57 3.57a1 1 0 0 1-.25 1z"/></svg></span><div style="line-height:32px;font-size:16px">555 014 2290</div></div>
    <div class="contact-line"><span class="sq"><svg width="18" height="13" viewBox="0 0 26 20"><rect width="26" height="20" fill="#fff"/><path d="M0 0l13 10L26 0" stroke="#8dc63f" stroke-width="2" fill="none"/></svg></span><div style="line-height:32px">hello@brightmoorhaven.com</div></div>
  </div>
  <div class="foot-col" style="left:629px">
    <h6>FOLLOW <span>US</span></h6>
    <ul class="follow">
      <li><span class="dot" style="background:#2a5a9a"></span>FRIENDLINE</li>
      <li><span class="dot" style="background:#1fa3d6"></span>CHIRPFEED</li>
      <li><span class="dot" style="background:#1878b0"></span>WORKGRID</li>
      <li><span class="dot" style="background:#d34836"></span>CIRCLEPLUS</li>
    </ul>
  </div>
  <div class="foot-brand"><span class="mark"></span>Brightmoor Haven</div>
</footer>
<div class="copyright">Copyright © 2016 Brightmoor Haven Real Estate. All rights reserved.</div>

</body>
</html>
```